Every Shelf Set Neatly or ESN Organized needs a business card design. ESN Organized is a professi

We need a business card design that is clean, sharp and conveys a sense of organization. I already have a logo.

Target Market(s)

Families (specifically mothers), small business owners, parents, seniors

Industry/Entity Type

Business

Contact Information for Business Card

My website is www.esnorganized-example.com and my Facebook page is http://www.sociallink-example.com/everyshelfsetneatly. The phone number is 418-552-7094 and I want to be listed as Lorna M. Pelham, Owner

Requirements
Must have
• My logo.

```html
<!DOCTYPE html>
<html lang="en">
<head>
<meta charset="utf-8">
<title>ESN Organized – Business Card</title>
<link rel="stylesheet" href="https://fonts.googleapis.com/css2?family=Montserrat:wght@400&family=Open+Sans:wght@400;600&display=swap">
<style>
  :root {
    --stage: #3b3532;
    --card: #0d0d0e;
    --card-edge: #1c1c1e;
    --accent: #1f7fd1;
    --text-light: #e9e9ea;
    --text-muted: #bdbdbf;
    --divider: #6a6a6d;
  }
  * { margin: 0; padding: 0; box-sizing: border-box; }
  html, body {
    width: 1200px; height: 814px; overflow: hidden;
    background: var(--stage);
  }
  .stage {
    width: 1200px; height: 814px;
    display: flex; align-items: center; justify-content: center; gap: 48px;
  }
  .card {
    width: 540px; height: 309px;
    background: var(--card);
    border: 1px solid var(--card-edge);
    border-radius: 4px;
    box-shadow: 0 14px 30px rgba(0,0,0,0.45);
    position: relative;
    color: var(--text-light);
  }
  /* Contact side */
  .card--contact { display: flex; align-items: center; }
  .brand-name {
    font-family: "Montserrat", sans-serif;
    font-weight: 400;
    letter-spacing: 0.12em;
    text-transform: uppercase;
    line-height: 1.35;
  }
  .card--contact .brand {
    width: 268px; padding-left: 40px;
    display: flex; align-items: center; gap: 10px;
  }
  .card--contact .brand-mark {
    width: 12px; height: 12px; flex: none;
    background: var(--accent);
  }
  .card--contact .brand-name { font-size: 14px; color: var(--accent); }
  .divider {
    width: 1px; height: 150px;
    background: var(--divider);
    margin: 0 26px 0 6px;
  }
  .contact { font-family: "Open Sans", sans-serif; }
  .contact-name {
    font-weight: 600; font-size: 17px; color: var(--accent);
  }
  .contact-role {
    font-size: 13px; color: var(--text-muted); margin: 2px 0 10px;
  }
  .contact-list { list-style: none; }
  .contact-list li {
    display: flex; align-items: center; gap: 7px;
    font-size: 12.5px; color: var(--text-light); line-height: 1.6;
  }
  .contact-list svg { width: 12px; height: 12px; flex: none; }
  .social-square {
    width: 11px; height: 11px; flex: none;
    background: var(--accent); border-radius: 1px;
  }
  /* Brand side */
  .card--brand {
    display: flex; flex-direction: column;
    align-items: center; justify-content: center;
  }
  .card--brand .brand-name {
    font-size: 24px; color: var(--text-light); text-align: center;
  }
  .web-address {
    margin-top: 34px;
    font-family: "Open Sans", sans-serif;
    font-size: 11px; letter-spacing: 0.32em;
    color: var(--text-muted);
  }
</style>
</head>
<body>
<main class="stage">
  <section class="card card--contact" aria-label="Business card, contact side">
    <div class="brand">
      <span class="brand-mark"></span>
      <span class="brand-name">Every Shelf<br>Set Neatly</span>
    </div>
    <div class="divider"></div>
    <div class="contact">
      <p class="contact-name">Lorna M. Pelham</p>
      <p class="contact-role">Owner</p>
      <ul class="contact-list">
        <li>
          <svg viewBox="0 0 24 24" aria-hidden="true"><path fill="#1f7fd1" d="M6.6 10.8a15.1 15.1 0 0 0 6.6 6.6l2.2-2.2c.3-.3.7-.4 1-.2 1.1.4 2.3.6 3.6.6.6 0 1 .4 1 1V20c0 .6-.4 1-1 1A17 17 0 0 1 3 4c0-.6.4-1 1-1h3.5c.6 0 1 .4 1 1 0 1.3.2 2.5.6 3.6.1.3 0 .7-.2 1z"/></svg>
          418-552-7094
        </li>
        <li>
          <svg viewBox="0 0 24 24" aria-hidden="true" fill="none" stroke="#1f7fd1" stroke-width="2.4"><circle cx="12" cy="12" r="9.5"/><path d="M2.5 12h19M12 2.5c3 3 3 16 0 19M12 2.5c-3 3-3 16 0 19"/></svg>
          www.esnorganized-example.com
        </li>
        <li>
          <span class="social-square"></span>
          everyshelfsetneatly
        </li>
      </ul>
    </div>
  </section>

  <section class="card card--brand" aria-label="Business card, brand side">
    <span class="brand-name">Every Shelf<br>Set Neatly</span>
    <p class="web-address">www.esnorganized-example.com</p>
  </section>
</main>
</body>
</html>
```